Stonebrace Business Card Design

The Stonebrace Co is an aggregate (crushing) equipment dealer serving Western Canadian provinces. Stonebrace is a distributor of aggregate equipment for different manufacturers.

We are looking to change and update the existing business card which has been used since the existence of the company. A copy of existing card has been attached for reference. The Stonebrace Co logo we want to remain the same and we want the green color to remain the same.

We are wanting something new with a different look. A refreshing card to show a new modern and updated look. No longer wanting to have the manufacturers on the back of the card but something more like our logo on the back of the card with a statement like "Crushing Solutions"

ideas could be:
- card can be different colors on front and back
- front or reverse of the card could possibly be the green color with the logo in black

Target Market(s)

Owners of Aggregate/Crushing companies

Contact Information for Business Card

see above

Requirements
Must have
• - logo to remain same along with same font within logo
• - green color to remain same
Nice to have
• as noted above under project description
Should not have

```html
<!DOCTYPE html>
<html lang="en">
<head>
<meta charset="utf-8">
<title>The Stonebrace Co – Business Card</title>
<link href="https://fonts.googleapis.com/css2?family=Arimo:wght@400;700&display=swap" rel="stylesheet">
<style>
  :root {
    --stage: #1b1b1b;
    --paper: #ffffff;
    --olive: #8a8b0a;
    --ink: #1a1a1a;
    --rule: #9a9a9a;
  }
  * { margin: 0; padding: 0; box-sizing: border-box; }
  html, body {
    width: 1200px; height: 900px; overflow: hidden;
    background: var(--stage);
    font-family: "Arimo", Arial, sans-serif;
  }
  .canvas { position: relative; width: 1200px; height: 900px; }
  .card {
    position: absolute; top: 170px; width: 347px; height: 561px;
    box-shadow: 3px 3px 6px rgba(0,0,0,0.6);
  }
  .card--front { left: 259px; background: var(--paper); }
  .card--back { left: 631px; background: var(--olive); }

  .brand-dot {
    position: absolute; border-radius: 50%;
  }
  .card--front .brand-dot {
    left: 143px; top: 100px; width: 60px; height: 60px; background: var(--olive);
  }
  .brand-name {
    position: absolute; left: 0; width: 100%; text-align: center;
    font-weight: 700; letter-spacing: 0.5px;
  }
  .card--front .brand-name { top: 185px; font-size: 23px; color: var(--ink); }

  .holder {
    position: absolute; top: 313px; left: 0; width: 100%;
    text-align: center; font-size: 21px; color: var(--olive);
  }
  .rule {
    position: absolute; left: 83px; width: 181px; height: 1px; background: var(--rule);
  }
  .rule--top { top: 349px; }
  .rule--bottom { top: 411px; }
  .address, .contacts {
    position: absolute; left: 0; width: 100%; text-align: center;
    font-size: 15.5px; line-height: 20px; color: var(--ink);
  }
  .address { top: 360px; }
  .contacts { top: 423px; }
  .contacts .label { color: var(--olive); font-weight: 700; }
  .contacts .web { color: var(--olive); }

  .card--back .brand-dot {
    left: 138px; top: 225px; width: 70px; height: 70px; background: var(--paper);
  }
  .card--back .brand-name { top: 310px; font-size: 22px; color: var(--paper); }
  .tagline {
    position: absolute; top: 470px; left: 0; width: 100%; text-align: center;
    font-size: 16px; font-weight: 700; letter-spacing: 2px; color: var(--paper);
  }
</style>
</head>
<body>
<main class="canvas">
  <section class="card card--front" aria-label="Card front">
    <span class="brand-dot" aria-hidden="true"></span>
    <p class="brand-name">THE STONEBRACE CO.</p>
    <p class="holder">DALE HARMON</p>
    <span class="rule rule--top"></span>
    <p class="address">5318-72B Avenue<br>Leduc, Alberta T9E 4R7</p>
    <span class="rule rule--bottom"></span>
    <p class="contacts">
      <span class="label">P:</span> 780.555.0142(Direct)<br>
      <span class="label">P:</span> 780.555.0186<br>
      <span class="label">F:</span> 780.555.0193<br>
      <span class="label">E:</span> dale@stonebr.com<br>
      <span class="web">www.stonebrace.ca</span>
    </p>
  </section>

  <section class="card card--back" aria-label="Card back">
    <span class="brand-dot" aria-hidden="true"></span>
    <p class="brand-name">THE STONEBRACE CO.</p>
    <p class="tagline">CRUSHING SOLUTIONS</p>
  </section>
</main>
</body>
</html>
```